Manual design

Hello,

I am looking for someone creative to help me design my Real Estate related manual. I am looking for something simple yet impressive. It would be designed around my logo and brand colors and I would also like it to have a local feel, perhaps with photos I could provide of my area/hometown. I am really shooting for an impressive company and branded look, while keeping it neat without too much going on.

I have the content that I would like to include, I am just struggling with the design of the manual in general.

I have attached a copy of my logo, my companys logo, and a publisher file of what I had previously done. Please do not think the design I previously used is something to work off of if you deem it better to use another feel. I am looking for originality, unless you can improve upon my old file. Any questions, please feel free to reach out to me.

The content in the provided brochure will remain the same, it is the design aspect I need help with. Thanks

Target Market(s)

My target market is home sellers aged 25-55, people usually selling their 1st or second home

Industry/Entity Type

Real Estate

Requirements
Must have
• -A simple to read design focused around my logo and colors
-A local sense
Should not have
• Drawings, only real photos

```html
<!DOCTYPE html>
<html lang="en">
<head>
<meta charset="utf-8">
<title>Intelligent Home Pricing</title>
<link href="https://fonts.googleapis.com/css2?family=Didact+Gothic&family=Quicksand:wght@500;700&display=swap" rel="stylesheet">
<style>
  :root {
    --navy: #0f2a63;
    --royal: #1c3f94;
    --ink: #2a2a2a;
    --body: #555555;
    --ghost: #efefef;
    --white: #ffffff;
    --sky-top: #2f5fb5;
    --sky-mid: #7fa6d8;
    --grass: #5f9a2c;
    --chart-light: #eef1f7;
    --chart-mid: #c9d3e8;
  }
  * { margin: 0; padding: 0; box-sizing: border-box; }
  html, body { width: 1200px; height: 848px; overflow: hidden; background: var(--white); }
  .spread { position: relative; width: 1200px; height: 848px; font-family: "Didact Gothic", sans-serif; color: var(--body); }

  /* left page */
  .cover-photo {
    position: absolute; left: 0; top: 0; width: 592px; height: 772px;
    background: linear-gradient(180deg, var(--sky-top) 0%, #5d8ccf 30%, var(--sky-mid) 55%, #b9cfe6 72%, #6d9a3c 82%, var(--grass) 100%);
  }
  .quote {
    position: absolute; left: 150px; top: 97px; width: 240px; text-align: center;
    color: var(--white); font-size: 20px; line-height: 27px;
  }
  .quote cite { display: block; font-family: "Quicksand", sans-serif; font-weight: 700; font-style: italic; font-size: 20px; }
  .agent-band {
    position: absolute; left: 0; top: 772px; width: 592px; height: 60px; background: var(--navy);
    color: var(--white);
  }
  .agent-mark { position: absolute; left: 18px; top: 16px; display: flex; align-items: center; gap: 5px; font-size: 11px; }
  .agent-mark i { width: 10px; height: 10px; background: var(--white); display: inline-block; }
  .agent-name { position: absolute; left: 108px; top: 4px; font-family: "Quicksand", sans-serif; font-weight: 700; font-size: 33px; line-height: 38px; }
  .agent-role { position: absolute; left: 109px; top: 41px; font-size: 11px; letter-spacing: .3px; }
  .agent-contact { position: absolute; right: 12px; top: 10px; text-align: right; font-size: 14px; line-height: 22px; letter-spacing: .8px; }

  /* right page */
  .ghost-title { position: absolute; left: 614px; top: -18px; font-size: 74px; color: var(--ghost); white-space: nowrap; letter-spacing: 1px; }
  .page-title { position: absolute; left: 621px; top: 40px; font-size: 31px; font-weight: 400; color: var(--ink); }
  .intro { position: absolute; left: 622px; top: 96px; width: 560px; font-size: 15.2px; line-height: 22.2px; }
  .subhead { font-family: "Quicksand", sans-serif; font-weight: 700; color: var(--ink); font-size: 18px; }
  .danger-head { position: absolute; left: 848px; top: 340px; }
  .danger-text { position: absolute; left: 850px; top: 368px; width: 340px; font-size: 15.3px; line-height: 22.3px; }
  .lowball-head { position: absolute; left: 621px; top: 693px; }
  .lowball-text { position: absolute; left: 622px; top: 719px; width: 565px; font-size: 15.3px; line-height: 22.3px; }
  .pricing-cycle {
    position: absolute; left: 618px; top: 356px; width: 222px; height: 250px;
    background: linear-gradient(180deg, var(--chart-light) 0%, var(--chart-mid) 55%, var(--chart-light) 100%);
  }
  .brokerage { position: absolute; left: 1058px; top: 790px; width: 120px; text-align: center; font-family: "Quicksand", sans-serif; font-weight: 700; color: var(--navy); font-size: 13px; line-height: 15px; }
</style>
</head>
<body>
<div class="spread">
  <section class="cover-page">
    <div class="cover-photo" role="img" aria-label="Photograph of two modern glass towers under a blue sky with a green lawn in front"></div>
    <blockquote class="quote">Price is what you pay.<br>Value is what you get.<cite>-Marcus Hale</cite></blockquote>
    <div class="agent-band">
      <div class="agent-mark"><i></i>whitford.ca</div>
      <div class="agent-name">Dana Whitford</div>
      <div class="agent-role">Multi-Award Winning Real Estate Professional</div>
      <div class="agent-contact">604-555-0182<br>homes@whitford.ca</div>
    </div>
  </section>

  <section class="content-page">
    <div class="ghost-title" aria-hidden="true">Home Pricing</div>
    <h1 class="page-title">Intelligent Home Pricing</h1>
    <p class="intro">Pricing your home properly is about 80% of the battle. With no guarantee any home is going to sell it's critical to price your home competitive, realistic and where it will attract the most amount of buyers. When pricing a home, I take into account real market values of similar homes that have sold around you, homes that tried to sell and were not successful, as well as our direct com-petition. Our goal is to be the home that sells, not the home that sells other homes.<br>When pricing a home, the market can choose to bear a price or reject it. Market value can change as a home remains on the mar-ket. By pricing the home at market value, a rising market will result in a sale, whereas a falling market must be monitored and the price adjusted accordingly.</p>

    <div class="pricing-cycle" role="img" aria-label="Illustration of the pricing cycle from market price to sale and price correction, with a time versus price chart below"></div>

    <h2 class="subhead danger-head">The dangers of overpricing a home</h2>
    <p class="danger-text">In a balanced or buyers market, overpricing your home can hurt you. As time marches on, if you do not price your home correct-ly from the start, you stand to lose value in your property. Buyers lose interest, and we lose our push. Like a swarm of bees, the first 30 days of a listing are so important. That is when all the buyers on the market are going to look at your home. After 30 days, all the buyers have seen your home and if too expensive or not offering enough value, they choose to purchase elsewhere. Now you are waiting for new buyers to come onto the market, and your chances of selling just went from 40% in the first 30 days, to 12%.</p>

    <h2 class="subhead lowball-head">What if they bring you a low ball offer?</h2>
    <p class="lowball-text">Who cares! Listing your home for sale is only an offer to buy. If you want $600,000 for your home and that is where we choose to list, even offers at $599,900 are available to turn away, until you get your price. It is better to<br>have 10 offers on the table, then no offers at all.</p>

    <div class="brokerage">HARBOURLINE<br>REALTY</div>
  </section>
</div>
</body>
</html>
```